Fern Lattice Table & Chair Rentals

We need a business card for a table and chair rental company. We rent tables and chairs for weddings, funerals, business events and parties. We want something that looks clean and elegant while not being too busy. We would like colors in the green and blue hues and avoiding anything orange. We want to make sure the font is large enough to be seen easily.

Target Market(s)

Wedding & Event Rentals

Industry/Entity Type

Events

Contact Information for Business Card

Fern Lattice, sales@fernlatticerentals.com, fernlatticerentals.com, 360-555-0182

Requirements
Must have
• Easy to read font
Should not have
• Orange anywhere in the design

```html
<!DOCTYPE html>
<html lang="en">
<head>
<meta charset="utf-8">
<title>Fern Lattice Table &amp; Chair Rentals – Business Card</title>
<link rel="stylesheet" href="https://fonts.googleapis.com/css2?family=Open+Sans:wght@400;600&display=swap">
<style>
  :root {
    --page-bg: #e9ebe8;
    --card-white: #ffffff;
    --ink: #1b1b1b;
    --text-grey: #333333;
    --leaf-green: #6f9a1c;
    --bark-brown: #3a3324;
    --bark-deep: #2a251a;
    --photo-light: #eef0ec;
    --photo-mid: #c9d2c4;
    --photo-green: #5f7d3a;
    --photo-blue: #b9cbd6;
  }
  * { box-sizing: border-box; margin: 0; padding: 0; }
  html, body {
    width: 1200px; height: 852px; overflow: hidden;
    background: var(--page-bg);
    font-family: "Open Sans", Arial, sans-serif;
  }
  .card {
    position: absolute;
    width: 560px; height: 320px;
    border-radius: 22px;
    overflow: hidden;
    box-shadow: 0 6px 18px rgba(0,0,0,0.18);
  }
  .card-front { left: 60px; top: 90px; }
  .card-back { left: 580px; top: 442px; background: var(--card-white); }

  .front-photo {
    position: absolute; inset: 0;
    background:
      radial-gradient(circle at 58% 52%, var(--photo-blue) 0, #dfe6e0 16%, transparent 30%),
      linear-gradient(160deg, var(--photo-light) 0%, var(--photo-mid) 45%, #8e9c80 72%, var(--photo-green) 100%);
  }
  .front-brand {
    position: absolute; left: 120px; top: 92px;
    color: var(--ink);
  }
  .brand-name {
    font-size: 58px; font-weight: 600; line-height: 1;
    letter-spacing: 0.5px;
  }
  .brand-tagline {
    margin-top: 14px;
    font-size: 24px; font-weight: 400;
  }

  .back-shape { position: absolute; inset: 0; }
  .back-brand {
    position: absolute; left: 34px; top: 226px;
    font-size: 38px; font-weight: 600; line-height: 1.2;
    color: var(--leaf-green);
    white-space: nowrap;
  }
  .contact-list {
    position: absolute; left: 288px; top: 96px;
    list-style: none;
  }
  .contact-item {
    display: flex; align-items: center; gap: 9px;
    font-size: 15.5px; line-height: 1.3; color: var(--text-grey);
    margin-bottom: 8px;
    white-space: nowrap;
  }
  .contact-icon { width: 15px; height: 15px; flex: none; }
</style>
</head>
<body>

<section class="card card-front">
  <div class="front-photo" role="img" aria-label="Soft-focus photo of white wedding chairs with hanging hydrangea flower balls"></div>
  <div class="front-brand">
    <div class="brand-name">Fern Lattice</div>
    <div class="brand-tagline">Table and Chair Rentals</div>
  </div>
</section>

<section class="card card-back">
  <svg class="back-shape" viewBox="0 0 560 320" preserveAspectRatio="none" aria-hidden="true">
    <defs>
      <linearGradient id="barkFill" x1="0" y1="0" x2="1" y2="1">
        <stop offset="0" stop-color="var(--bark-brown)"/>
        <stop offset="1" stop-color="var(--bark-deep)"/>
      </linearGradient>
    </defs>
    <path d="M0 0 H200 C225 80 285 170 310 320 H0 Z" fill="url(#barkFill)"/>
    <path d="M200 0 C225 80 285 170 310 320" fill="none" stroke="var(--leaf-green)" stroke-width="7"/>
  </svg>

  <div class="back-brand">Fern Lattice</div>

  <ul class="contact-list">
    <li class="contact-item">
      <svg class="contact-icon" viewBox="0 0 16 16" aria-hidden="true">
        <path d="M2 5c0-2 2-3 6-3s6 1 6 3v1h-3V5H5v1H2z M4 7h8l2 6H2z" fill="var(--leaf-green)"/>
      </svg>
      360-555-0182
    </li>
    <li class="contact-item">
      <svg class="contact-icon" viewBox="0 0 16 16" aria-hidden="true">
        <rect x="1" y="3" width="14" height="10" rx="1" fill="var(--leaf-green)"/>
        <path d="M1.5 3.5 8 9l6.5-5.5" fill="none" stroke="#fff" stroke-width="1.3"/>
      </svg>
      sales@fernlatticerentals.com
    </li>
    <li class="contact-item">
      <svg class="contact-icon" viewBox="0 0 16 16" aria-hidden="true">
        <circle cx="8" cy="8" r="7" fill="var(--leaf-green)"/>
        <path d="M1 8h14M8 1c-3 3-3 11 0 14M8 1c3 3 3 11 0 14" fill="none" stroke="#fff" stroke-width="1"/>
      </svg>
      www.fernlatticerentals.com
    </li>
  </ul>
</section>

</body>
</html>
```